Consulting company requires a logo and business card design

I require a logo/business card design for a new company based in Sexsmith Alberta called TallMarsh Integrity Consulting Ltd. I plan to provide the following services: Construction management/inspection for the oil and gas industry, as well as general consulting for Asset Management, fleet management, etc. Have attached a copy of resume for use as guide for

Target Market(s)

Businesses within the oil and gas production, construction and shipping industry

Industry/Entity Type

Oil And Gas

Contact Information for Business Card

Believe should highlight, services offered, safety, quality,

Logo Text

TallMarsh Integrity Consulting (TMIC) ?

Font styles to use
Script

Requirements
Must have
• Open to all options

```html
<!DOCTYPE html>
<html lang="en">
<head>
<meta charset="utf-8">
<title>TallMarsh Integrity Consulting Ltd – Business Card</title>
<link rel="stylesheet" href="https://fonts.googleapis.com/css2?family=Lato:wght@400;700&display=swap">
<style>
  :root {
    --bg: #ece9e4;
    --amber-light: #ffd300;
    --amber-deep: #fbaa1a;
    --amber-text: #f7b500;
    --ink: #4a4a4a;
    --ink-dark: #222222;
    --paper: #ffffff;
    --shadow: 0 10px 28px rgba(0, 0, 0, 0.18);
  }
  * { box-sizing: border-box; margin: 0; padding: 0; }
  html, body {
    width: 1200px;
    height: 900px;
    overflow: hidden;
    background: var(--bg);
    font-family: "Lato", Arial, sans-serif;
  }
  .stage {
    position: relative;
    width: 1200px;
    height: 900px;
    display: flex;
    align-items: center;
    justify-content: center;
    gap: 40px;
  }
  .card {
    position: relative;
    width: 540px;
    height: 309px;
    border-radius: 2px;
    box-shadow: var(--shadow);
    overflow: hidden;
  }

  /* Front face */
  .card-front {
    background: linear-gradient(160deg, var(--amber-light) 0%, var(--amber-deep) 100%);
  }
  .front-name {
    position: absolute;
    right: 34px;
    bottom: 62px;
    text-align: right;
    color: var(--paper);
    font-weight: 400;
  }
  .front-name .line-main {
    display: block;
    font-size: 31px;
    letter-spacing: 0.2px;
    line-height: 1.1;
  }
  .front-name .line-sub {
    display: block;
    font-size: 21px;
    letter-spacing: 9px;
    margin-top: 4px;
    margin-right: -9px;
  }

  /* Back face */
  .card-back {
    background: var(--paper);
  }
  .brand {
    position: absolute;
    left: 40px;
    top: 36px;
    display: flex;
    align-items: center;
    gap: 12px;
    color: var(--ink);
    font-weight: 700;
  }
  .brand-dot {
    width: 30px;
    height: 30px;
    border-radius: 50%;
    background: var(--amber-text);
    flex: none;
  }
  .brand-name .line-main {
    display: block;
    font-size: 23px;
    line-height: 1.1;
  }
  .brand-name .line-sub {
    display: block;
    font-size: 17px;
    letter-spacing: 7px;
    margin-top: 3px;
  }
  .contact {
    position: absolute;
    left: 318px;
    top: 128px;
    color: var(--ink-dark);
    font-size: 12.5px;
    line-height: 1.35;
  }
  .person-name {
    color: var(--amber-text);
    font-size: 16px;
    font-weight: 400;
  }
  .person-role { margin-bottom: 14px; }
  .address { margin-bottom: 14px; }
  .contact-list { list-style: none; }
  .contact-list li {
    display: flex;
    align-items: center;
    gap: 10px;
    margin-bottom: 2px;
  }
  .contact-list svg {
    width: 11px;
    height: 11px;
    flex: none;
    fill: var(--amber-text);
  }
</style>
</head>
<body>
<main class="stage">
  <section class="card card-front" aria-label="Business card front">
    <h1 class="front-name">
      <span class="line-main">TallMarsh Integrity</span>
      <span class="line-sub">Consulting Ltd</span>
    </h1>
  </section>

  <section class="card card-back" aria-label="Business card back">
    <div class="brand">
      <span class="brand-dot" aria-hidden="true"></span>
      <p class="brand-name">
        <span class="line-main">TallMarsh Integrity</span>
        <span class="line-sub">Consulting Ltd</span>
      </p>
    </div>

    <div class="contact">
      <p class="person-name">Daniel Hartley</p>
      <p class="person-role">Managing Director</p>
      <p class="address">4820, Ridgeway Avenue<br>Northvale, 204518.</p>
      <ul class="contact-list">
        <li>
          <svg viewBox="0 0 24 24" aria-hidden="true"><path d="M6.6 10.8a15.1 15.1 0 0 0 6.6 6.6l2.2-2.2a1 1 0 0 1 1-.25 11.4 11.4 0 0 0 3.6.57 1 1 0 0 1 1 1V20a1 1 0 0 1-1 1A17 17 0 0 1 3 4a1 1 0 0 1 1-1h3.5a1 1 0 0 1 1 1c0 1.25.2 2.45.57 3.57a1 1 0 0 1-.25 1z"/></svg>
          <span>044-318 562 907</span>
        </li>
        <li>
          <svg viewBox="0 0 24 24" aria-hidden="true"><path d="M2 5h20v14H2z M4 7v.4l8 5 8-5V7l-8 5z" fill-rule="evenodd"/></svg>
          <span>info@tallmarshic.com</span>
        </li>
        <li>
          <svg viewBox="0 0 24 24" aria-hidden="true"><path d="M10.6 13.4a1 1 0 0 0 1.4 0l4.6-4.6a3 3 0 0 0-4.2-4.2l-2 2 1.4 1.4 2-2a1 1 0 0 1 1.4 1.4L10.6 12a1 1 0 0 0 0 1.4zM13.4 10.6a1 1 0 0 0-1.4 0l-4.6 4.6a3 3 0 0 0 4.2 4.2l2-2-1.4-1.4-2 2a1 1 0 0 1-1.4-1.4l4.6-4.6a1 1 0 0 0 0-1.4z"/></svg>
          <span>www.tallmarshic.com</span>
        </li>
      </ul>
    </div>
  </section>
</main>
</body>
</html>
```